The K7 Momentum Collective Website

We have a pitch deck and messaging drafted. Target audience is academic institutions and VC investors that have seed money in start ups.

Need a basic website

Industry/Entity Type

LIfe Science, Diagnostic, medical device.

Coding

Coded - Design and coding required

Number of Pages Required

5+ page

```html
<!DOCTYPE html>
<html lang="en">
<head>
<meta charset="utf-8">
<title>K7 Momentum Collective</title>
<link rel="stylesheet" href="https://fonts.googleapis.com/css2?family=Josefin+Sans:wght@600;700&family=Nunito+Sans:wght@400;600;700;800&display=swap">
<style>
:root{
  --teal:#4fb3c9;
  --teal-dark:#3a9fb6;
  --ink:#1c1c1c;
  --text:#4a4a4a;
  --soft:#f5f3f3;
  --pale:#eef6f8;
  --white:#ffffff;
}
*{margin:0;padding:0;box-sizing:border-box}
html,body{width:1200px;height:3542px;overflow:hidden}
body{position:relative;font-family:"Nunito Sans",sans-serif;color:var(--text);background:var(--white)}
.abs{position:absolute}
.brand{font-family:"Nunito Sans",sans-serif;font-weight:700;font-size:17px;letter-spacing:.4px;color:var(--ink);white-space:nowrap}
.btn{position:absolute;display:flex;align-items:center;justify-content:center;background:var(--teal);color:var(--white);font-weight:800;font-size:13px;letter-spacing:.3px;text-transform:uppercase}
.sec-title{font-family:"Josefin Sans",sans-serif;font-weight:700;color:var(--ink);font-size:20px;letter-spacing:.8px;text-transform:uppercase}
.rule{position:absolute;height:2px;background:var(--teal)}
/* header */
.site-header{position:absolute;left:0;top:0;width:1200px;height:69px;background:var(--white)}
.site-header .brand{left:132px;top:24px}
.nav a{position:absolute;top:28px;font-size:12px;font-weight:600;color:var(--ink);text-decoration:none;letter-spacing:.2px}
.nav-marker{position:absolute;left:599px;top:69px;width:0;height:0;border-left:9px solid transparent;border-right:9px solid transparent;border-top:9px solid var(--white);z-index:2}
/* hero */
.hero{position:absolute;left:0;top:69px;width:1200px;height:474px;background:linear-gradient(90deg,#2f2c28 0%,#4b4741 40%,#8a8580 70%,#6e6b63 100%)}
.hero-title{position:absolute;left:131px;top:74px;font-family:"Josefin Sans",sans-serif;font-weight:700;font-size:42px;line-height:48px;color:var(--white);letter-spacing:1px}
.hero-text{position:absolute;left:131px;top:239px;width:400px;font-size:14.5px;line-height:21px;color:var(--white)}
.hero .btn{left:132px;top:323px;width:120px;height:41px}
.hero-arrows{position:absolute;left:131px;top:404px}
/* pillars */
.pillars{position:absolute;left:0;top:543px;width:1200px;height:214px;background:var(--teal)}
.pillar{position:absolute;top:40px;color:var(--white)}
.pillar h3{font-family:"Josefin Sans",sans-serif;font-weight:700;font-size:27px;margin-bottom:14px}
.pillar p{font-size:14.5px;line-height:21px;width:180px}
/* plan */
.plan-photo{position:absolute;left:132px;top:893px;width:389px;height:506px;background:linear-gradient(160deg,#d9dcdc,#a9adae 60%,#6b6d6e)}
.plan-item{position:absolute;left:569px;width:500px}
.plan-icon{position:absolute;left:0;top:0;width:56px;height:56px;border-radius:50%;background:var(--teal);display:flex;align-items:center;justify-content:center}
.plan-item h4{position:absolute;left:72px;top:-4px;font-size:14px;font-weight:700;color:var(--teal);letter-spacing:.4px;white-space:nowrap}
.plan-item p{position:absolute;left:73px;top:18px;width:410px;font-size:12.5px;line-height:16px;color:var(--text)}
/* welcome */
.welcome{position:absolute;left:0;top:1471px;width:1200px;height:447px;background:var(--soft)}
.welcome-photo{position:absolute;left:590px;top:0;width:610px;height:447px;background:linear-gradient(170deg,#7c6a5a,#b9a08a 45%,#d9cfc4 70%,#6d5f52)}
.welcome-text{position:absolute;left:132px;top:117px;width:401px;font-size:14px;line-height:20.7px;text-align:justify}
/* solution */
.solution-photo{position:absolute;left:148px;top:1979px;width:378px;height:472px;background:linear-gradient(180deg,#d6dde3,#b7c3cc 45%,#4f5a63 75%,#2e353b)}
.solution-lead{position:absolute;left:589px;top:2040px;width:476px;font-size:14px;line-height:21px;text-align:justify}
.problems{position:absolute;left:590px;top:2111px;width:478px;height:259px;background:var(--pale);padding:26px 30px 0 29px;font-size:13.5px;line-height:18px}
.problems ul{list-style:none;margin:14px 0 0 0}
.problems li{position:relative;padding-left:34px;margin-bottom:18px}
.problems li::before{content:"";position:absolute;left:14px;top:5px;border-left:5px solid var(--teal);border-top:4px solid transparent;border-bottom:4px solid transparent}
.problems .note{margin-top:24px}
.solution-close{position:absolute;left:589px;top:2395px;width:478px;font-size:14px;line-height:21px}
/* team */
.team{position:absolute;left:0;top:2517px;width:1200px;height:672px;background:var(--soft)}
.card{position:absolute;top:120px;width:297px;height:500px;background:var(--white);text-align:center}
.card .photo{width:297px;height:199px}
.card h5{margin-top:22px;font-size:13px;font-weight:800;color:var(--ink);letter-spacing:.4px}
.card .role{margin-top:4px;font-size:12.5px;letter-spacing:.6px;color:var(--ink)}
.card .focus{margin-top:14px;font-size:12px;line-height:16.5px;padding:0 20px}
.card .bio{margin-top:14px;font-size:12px;line-height:16.5px;padding:0 34px;height:68px}
.card .reach{margin-top:10px;font-size:12px}
.card .btn{position:relative;margin:18px auto 0;width:85px;height:29px;font-size:11.5px}
/* footer */
.site-footer{position:absolute;left:0;top:3189px;width:1200px;height:353px;background:var(--teal);color:var(--white)}
.site-footer .brand{left:132px;top:125px;color:var(--white)}
.foot-head{position:absolute;top:40px;font-size:14px;font-weight:800;letter-spacing:.4px}
.foot-rule{position:absolute;top:65px;height:2px;background:var(--white)}
.foot-row{position:absolute;font-size:12px;line-height:15.5px}
.foot-ico{position:absolute;width:24px;height:24px;border-radius:50%;background:var(--white);display:flex;align-items:center;justify-content:center}
.foot-menu{position:absolute;left:722px;top:92px;font-size:12px;line-height:20px;list-style:none}
.foot-divider{position:absolute;left:132px;top:275px;width:935px;height:1px;background:rgba(255,255,255,.45)}
.copyright{position:absolute;left:0;width:1200px;top:308px;text-align:center;font-size:12px}
</style>
</head>
<body>

<header class="site-header">
  <div class="brand abs">K7 Momentum Collective</div>
  <nav class="nav">
    <a style="left:590px">HOME</a>
    <a style="left:655px">ABOUT US</a>
    <a style="left:749px">SERVICES</a>
    <a style="left:832px">SOLUTIONS</a>
    <a style="left:930px">BLOG</a>
    <a style="left:991px">CONTACT US</a>
  </nav>
</header>
<div class="nav-marker"></div>

<section class="hero" role="img" aria-label="Two business professionals in conversation at a laptop in a modern lounge">
  <h1 class="hero-title">ACCELERATING<br>YOUR INNOVATIVE<br>IP TO MARKET!</h1>
  <p class="hero-text">The K7 Momentum Collective (K7) rapidly brings innovative and transformational IP to market by assisting with all elements of a company’s development.</p>
  <a class="btn">Read More</a>
  <svg class="hero-arrows" width="50" height="20" viewBox="0 0 50 20"><path d="M10 2 L3 10 L10 18" fill="none" stroke="#fff" stroke-width="2"/><path d="M36 2 L43 10 L36 18" fill="none" stroke="#fff" stroke-width="2"/></svg>
</section>

<section class="pillars">
  <div class="pillar" style="left:133px"><h3>We Are...</h3><p>experienced in strategic business planning and execution, and operational excellence</p></div>
  <div class="pillar" style="left:390px"><h3>We Have...</h3><p style="width:170px">100 years of collective experiences and vast network of people, partners, and processes</p></div>
  <div class="pillar" style="left:650px"><h3>We Can...</h3><p style="width:185px">serve as the initial executive team to ensure strategic alignment with a focus on marketplace</p></div>
  <div class="pillar" style="left:891px"><h3>We Will...</h3><p style="width:180px">remove the uncertainty and confusion common in the initial stages of a company’s formation.</p></div>
</section>

<section class="plan">
  <h2 class="sec-title abs" style="left:0;width:1200px;text-align:center;top:804px">K7 Plan Elements</h2>
  <div class="rule" style="left:582px;top:846px;width:36px"></div>
  <div class="plan-photo" role="img" aria-label="Businessman in a suit reading a tablet at a desk"></div>

  <div class="plan-item" style="top:894px">
    <div class="plan-icon"><svg width="26" height="26" viewBox="0 0 26 26"><rect x="6" y="3" width="14" height="19" rx="2" fill="none" stroke="#fff" stroke-width="2"/><path d="M9 9h8M9 13h8M9 17h5" stroke="#fff" stroke-width="2"/></svg></div>
    <h4>EXECUTIVE SUMMARY</h4>
    <p>Articulates a brief snapshot of the business model/plan, including name, location, products or services, mission statement, and organizational values/ cultural beliefs.</p>
  </div>
  <div class="plan-item" style="top:992px">
    <div class="plan-icon"><svg width="26" height="26" viewBox="0 0 26 26"><rect x="8" y="3" width="10" height="20" fill="none" stroke="#fff" stroke-width="2"/><path d="M11 7h1M14 7h1M11 11h1M14 11h1M11 15h1M14 15h1" stroke="#fff" stroke-width="2"/></svg></div>
    <h4>COMPANY DESCRIPTION</h4>
    <p>Describes a high-level view of the business nature, customer need being met, history, legality, short term, and long-term goals</p>
  </div>
  <div class="plan-item" style="top:1075px">
    <div class="plan-icon"><svg width="26" height="26" viewBox="0 0 26 26"><circle cx="12" cy="11" r="7" fill="none" stroke="#fff" stroke-width="2"/><path d="M17 16l6 6" stroke="#fff" stroke-width="3"/></svg></div>
    <h4>MARKET ANALYSIS</h4>
    <p>Displays research and plan to reach the target demographic as well as the size, direction, and competitors in the overall industry.</p>
  </div>
  <div class="plan-item" style="top:1158px">
    <div class="plan-icon"><svg width="26" height="26" viewBox="0 0 26 26"><rect x="5" y="5" width="16" height="18" rx="2" fill="none" stroke="#fff" stroke-width="2"/><rect x="10" y="3" width="6" height="4" fill="#fff"/><path d="M9 14l3 3 5-6" fill="none" stroke="#fff" stroke-width="2"/></svg></div>
    <h4>OPERATIONS/STRATEGY</h4>
    <p>Displays research and plan to reach the target demographic as well as the size, direction, and competitors in the overall industry.</p>
  </div>
  <div class="plan-item" style="top:1243px">
    <div class="plan-icon"><svg width="26" height="26" viewBox="0 0 26 26"><rect x="4" y="13" width="4" height="9" fill="#fff"/><rect x="10" y="8" width="4" height="14" fill="#fff"/><rect x="16" y="4" width="6" height="18" fill="none" stroke="#fff" stroke-width="2"/></svg></div>
    <h4>FINANCIALS</h4>
    <p>Details estimates of all the important, financial documents, including balance sheet, cash flow, statement, capital, expenditure, budget, and income statement.</p>
  </div>
  <div class="plan-item" style="top:1343px">
    <div class="plan-icon"><svg width="26" height="26" viewBox="0 0 26 26"><circle cx="8" cy="7" r="3" fill="#fff"/><circle cx="18" cy="7" r="3" fill="#fff"/><circle cx="13" cy="10" r="3" fill="#fff"/><rect x="5" y="11" width="6" height="10" rx="2" fill="#fff"/><rect x="15" y="11" width="6" height="10" rx="2" fill="#fff"/><rect x="10" y="14" width="6" height="9" rx="2" fill="#fff"/></svg></div>
    <h4>ORGANIZATION &amp; MANAGEMENT TEAM</h4>
    <p>Shows the company structure as well as identifying divisions and key management personnel.</p>
  </div>
</section>

<section class="welcome">
  <h2 class="sec-title abs" style="left:132px;top:49px;font-size:17px;white-space:nowrap">Welcome to K7 Momentum Collective</h2>
  <div class="rule" style="left:132px;top:85px;width:106px"></div>
  <p class="welcome-text">The K7 Momentum Collective (K7) is a group of experienced executives whose careers have been focused on taking innovative ideas to market by strategically navigating the buildout of best-in-class life science and diagnostic organizations. This experience makes us uniquely equipped to be involved in all aspects of your due diligence on new or existing investments (business analysis, industry thesis, competitive landscape, business/pricing model, and financial modeling as it relates to validation of the assumptions in the model to determine the return expectations).</p>
  <a class="btn" style="left:133px;top:353px;width:120px;height:41px">Read More</a>
  <div class="welcome-photo" role="img" aria-label="Smiling team gathered around a table covered in charts and sticky notes"></div>
</section>

<section class="solution">
  <div class="solution-photo" role="img" aria-label="Presenter in a suit holding a report beside a window and a plant"></div>
  <h2 class="sec-title abs" style="left:589px;top:1979px">The Solution</h2>
  <div class="rule" style="left:589px;top:2014px;width:37px"></div>
  <p class="solution-lead">K7 was started to solve significant problems associated with rapidly bringing innovative and transformational IP to market.</p>
  <div class="problems">
    <p>These costly problems include</p>
    <ul>
      <li>Incomplete strategic planning,</li>
      <li>Difficulty finding leadership,</li>
      <li>Not able to differentiate a product or service from others that are already available, and Ignoring the needs of customer.</li>
    </ul>
    <p class="note">(Capital shortages, poor locations, and scaling too soon can also cause a start-up to have problems.)</p>
  </div>
  <p class="solution-close">The K7 Plan is unique to your organizational needs and secures the right people, partners, and processes to ensure an efficient start-up with strategic growth, and access to funding sources to help scale the business.</p>
</section>

<section class="team">
  <h2 class="sec-title abs" style="left:0;width:1200px;text-align:center;top:41px">Meet the Team</h2>
  <div class="rule" style="left:582px;top:76px;width:36px"></div>

  <article class="card" style="left:132px">
    <div class="photo" role="img" aria-label="Portrait of partner Dana Whitlow" style="background:linear-gradient(160deg,#e6e4df,#b8ab9c 60%,#8a6d5c)"></div>
    <h5>DANA WHITLOW</h5><p class="role">PARTNER</p>
    <p class="focus">Marketing, Commercial Development, Product Development, Growth Strategy</p>
    <p class="bio">30+ years of marketing, sales, product development, and operations executive leader in the life science and diagnostic industries.</p>
    <p class="reach">(555) 014-2201 &nbsp;| &nbsp;dana@k7mc.com</p>
    <a class="btn">View Bio</a>
  </article>
  <article class="card" style="left:451px">
    <div class="photo" role="img" aria-label="Portrait of partner Marie Lindqvist" style="background:linear-gradient(160deg,#4b5f7a,#b39478 55%,#d9c3a3)"></div>
    <h5>MARIE LINDQVIST</h5><p class="role">PARTNER</p>
    <p class="focus">Regulatory, Quality, Product Development, Operations</p>
    <p class="bio">30+ years working in diagnostic and medical device area with focus on creative solutions to bring product to market.</p>
    <p class="reach">(555) 017-3382 &nbsp;| &nbsp;marie@k7mc.com</p>
    <a class="btn">View Bio</a>
  </article>
  <article class="card" style="left:770px">
    <div class="photo" role="img" aria-label="Portrait of partner Owen Radcliffe" style="background:linear-gradient(160deg,#8e8f8c,#b59c8c 55%,#5c5a57)"></div>
    <h5>OWEN RADCLIFFE</h5><p class="role">PARTNER</p>
    <p class="focus">Board Development, Funding, Back-office Set-up, Operations</p>
    <p class="bio" style="padding:0 22px">30+ years accomplished CEO and well-rounded executive with more than 25 years of experience in medical devices, research tools and diagnostics.</p>
    <p class="reach">(555) 019-4473 &nbsp;| &nbsp;owen@k7mc.com</p>
    <a class="btn">View Bio</a>
  </article>
</section>

<footer class="site-footer">
  <div class="brand abs">K7 Momentum Collective</div>

  <div class="foot-head" style="left:418px">CONTACT US</div>
  <div class="foot-rule" style="left:418px;width:192px"></div>
  <div class="foot-ico" style="left:418px;top:97px"><svg width="12" height="14" viewBox="0 0 12 14"><path d="M6 13C2 8 1 6 1 5a5 5 0 0 1 10 0c0 1-1 3-5 8z" fill="#4fb3c9"/><circle cx="6" cy="5" r="1.8" fill="#fff"/></svg></div>
  <div class="foot-row" style="left:451px;top:93px">418 Bayview Ave., Ste 210<br>Port Alder, Florida 30410</div>
  <div class="foot-ico" style="left:418px;top:148px"><svg width="12" height="12" viewBox="0 0 12 12"><path d="M2 1l3 0 1 3-2 1a7 7 0 0 0 3 3l1-2 3 1v3c-6 0-10-4-10-9z" fill="#4fb3c9"/></svg></div>
  <div class="foot-row" style="left:451px;top:144px">Call Us<br>+1 555 010 2030</div>
  <div class="foot-ico" style="left:418px;top:200px"><svg width="12" height="10" viewBox="0 0 12 10"><rect x="0.5" y="0.5" width="11" height="9" fill="#4fb3c9"/><path d="M1 1l5 4 5-4" fill="none" stroke="#fff" stroke-width="1.2"/></svg></div>
  <div class="foot-row" style="left:451px;top:196px">E mail Us<br>hello@ k7momentumcollective.com</div>

  <div class="foot-head" style="left:720px">MENU</div>
  <div class="foot-rule" style="left:720px;width:107px"></div>
  <ul class="foot-menu"><li>Home</li><li>About Us</li><li>Services</li><li>Solutions</li><li>Blog</li><li>Contact Us</li></ul>

  <div class="foot-head" style="left:921px">FOLLOW US</div>
  <div class="foot-rule" style="left:921px;width:107px"></div>
  <div class="foot-ico" style="left:921px;top:105px"></div>
  <div class="foot-row" style="left:956px;top:101px">Like us on<br>CIRCLEBOOK</div>
  <div class="foot-ico" style="left:921px;top:156px"></div>
  <div class="foot-row" style="left:956px;top:152px">Follow us on<br>CHIRPER</div>
  <div class="foot-ico" style="left:921px;top:207px"></div>
  <div class="foot-row" style="left:956px;top:203px">Follow us on<br>LINKWORK</div>

  <div class="foot-divider"></div>
  <p class="copyright">Copyright © 2023 All Rights Reserved</p>
</footer>

</body>
</html>
```